HearthMile business card and stationary design

We are looking for a simple yet elegant design for our mortgage company business card and stationary.

The card should include:
Name (Marcus Pell)
Title (CEO)
Phone Number (732-555-0182)
Address (48 Birchwell Court, Suite 314, Larkmoor, NJ 08841)
Email (email@hearthmile.example)
"NMLS" i.e. (NMLS 61947)
"Company NMLS" (Company NMLS 274615)

Contact Information for Business Card

See above

```html
<!DOCTYPE html>
<html lang="en">
<head>
<meta charset="utf-8">
<title>HearthMile Business Card</title>
<link rel="stylesheet" href="https://fonts.googleapis.com/css2?family=Montserrat:wght@500;600;700&family=Open+Sans:wght@400;600&display=swap">
<style>
  :root {
    --canvas-bg: #b9bcbf;
    --card-white: #ffffff;
    --navy: #141f2b;
    --brand-blue: #1aa3e8;
    --card-back-blue: #00acee;
    --emboss-blue: #0b7fd0;
    --text-light: #eef2f6;
    --divider: #7c8794;
  }
  * { box-sizing: border-box; margin: 0; padding: 0; }
  html, body {
    width: 1200px; height: 800px; overflow: hidden;
    background: radial-gradient(ellipse at 40% 30%, #d6d8da 0%, var(--canvas-bg) 100%);
  }
  .canvas {
    position: relative; width: 1200px; height: 800px;
    display: flex; align-items: center; justify-content: center; gap: 40px;
  }
  .card {
    position: relative; width: 540px; height: 309px;
    border-radius: 22px; overflow: hidden;
    box-shadow: 0 14px 30px rgba(0,0,0,0.22), 0 3px 8px rgba(0,0,0,0.15);
  }
  .card-front { background: var(--card-white); }
  .card-front .backdrop { position: absolute; inset: 0; }
  .wordmark {
    position: absolute; left: 46px; top: 58px;
    font-family: "Montserrat", sans-serif; font-weight: 600;
    font-size: 52px; letter-spacing: -0.5px; color: var(--navy);
  }
  .identity {
    position: absolute; right: 290px; top: 190px; width: 230px;
    text-align: right; color: var(--text-light);
    font-family: "Open Sans", sans-serif;
  }
  .identity .name {
    font-family: "Montserrat", sans-serif; font-weight: 700;
    font-size: 22px; line-height: 24px;
  }
  .identity .title {
    font-size: 12px; color: var(--brand-blue); line-height: 16px; margin-bottom: 4px;
  }
  .identity .address { font-size: 13px; line-height: 17px; }
  .divider {
    position: absolute; left: 266px; top: 188px; width: 1px; height: 100px;
    background: var(--divider);
  }
  .contact {
    position: absolute; left: 282px; top: 190px;
    font-family: "Open Sans", sans-serif; font-size: 13px; line-height: 19px;
    color: var(--text-light); list-style: none;
  }
  .contact li { display: flex; align-items: center; gap: 7px; white-space: nowrap; }
  .contact .icon { width: 11px; height: 11px; flex: none; fill: var(--brand-blue); }
  .contact .icon-mail { fill: none; stroke: var(--brand-blue); stroke-width: 2.5; }
  .card-back {
    background: linear-gradient(100deg, #12b6f4 0%, var(--card-back-blue) 60%, #00a6e8 100%);
    display: flex; align-items: center; justify-content: center;
  }
  .card-back .wordmark-large {
    font-family: "Montserrat", sans-serif; font-weight: 600;
    font-size: 64px; letter-spacing: -0.5px; color: var(--emboss-blue);
  }
</style>
</head>
<body>
<main class="canvas">
  <section class="card card-front">
    <svg class="backdrop" width="540" height="309" viewBox="0 0 540 309">
      <path d="M0 178 H318 L368 132 H420 L470 92 H540 V309 H0 Z" fill="var(--navy)"/>
      <polyline points="0,170 315,170 365,124 417,124 467,84 540,84" fill="none" stroke="var(--brand-blue)" stroke-width="3"/>
    </svg>
    <div class="wordmark">HearthMile</div>
    <div class="identity">
      <div class="name">Marcus Pell</div>
      <div class="title">CEO</div>
      <div class="address">48 Birchwell Court<br>Suite 314<br>Larkmoor, NJ 08841</div>
    </div>
    <div class="divider"></div>
    <ul class="contact">
      <li>Company NMLS 274615</li>
      <li>NMLS 61947</li>
      <li><svg class="icon" viewBox="0 0 24 24"><path d="M6.6 10.8a15.1 15.1 0 0 0 6.6 6.6l2.2-2.2a1 1 0 0 1 1-.25 11.4 11.4 0 0 0 3.6.57 1 1 0 0 1 1 1V20a1 1 0 0 1-1 1A17 17 0 0 1 3 4a1 1 0 0 1 1-1h3.5a1 1 0 0 1 1 1c0 1.25.2 2.45.57 3.57a1 1 0 0 1-.25 1z"/></svg>732-555-0182</li>
      <li><svg class="icon icon-mail" viewBox="0 0 24 24"><rect x="2" y="5" width="20" height="14"/><polyline points="2,5 12,13 22,5"/></svg>email@hearthmile.example</li>
      <li><svg class="icon" viewBox="0 0 24 24"><circle cx="12" cy="12" r="10"/></svg>hearthmile.example</li>
    </ul>
  </section>
  <section class="card card-back">
    <div class="wordmark-large">HearthMile</div>
  </section>
</main>
</body>
</html>
```